Wholesale food company needs a package for Carp boilies (fishing)

We need a (5kg) doypack with handle design for a new brand here in the BENELUX called Tolvo Lures. We already have a logo but we need a flashing design to promote it on shows and webshops. The design must also include some transparant places so you can see the product inside. We have added the logo and the website is www.tolvolures.nl. You can look for an impression at http://marwick-goods.nl/product-category/baits/specials/

Target Market(s)

Carpf fishing and coarse angling

Industry/Entity Type

It Company

Requirements
Must have
• A slogan that suits both types of fishing.
• Extra information doypack:
• Material: PET/PE
• Thickness: 12µ/120µ
• Size: B 320 x H 450 MM

```html
<!DOCTYPE html>
<html lang="en">
<head>
<meta charset="utf-8">
<title>Tolvo Lures – Boilies Doypack</title>
<link rel="stylesheet" href="https://fonts.googleapis.com/css2?family=Exo+2:wght@700&family=Roboto:wght@700&display=swap">
<style>
  :root {
    --bg: #ffffff;
    --orange: #f0921a;
    --orange-dark: #d8760c;
    --green: #6ea83a;
    --green-light: #8cc24a;
    --navy: #1b1a6e;
    --navy-deep: #0f0e45;
    --silver: #d9dbe0;
    --white: #ffffff;
    --logo-blue: #2f8fc7;
    --boilie-dark: #5a4128;
    --boilie-mid: #9a7a55;
    --boilie-light: #d8c6a6;
  }
  html, body {
    margin: 0;
    padding: 0;
    width: 1200px;
    height: 957px;
    overflow: hidden;
    background: var(--bg);
  }
  .canvas {
    position: relative;
    width: 1200px;
    height: 957px;
  }
  .doypack {
    position: absolute;
    left: 412px;
    top: 105px;
    width: 456px;
    height: 730px;
  }
  .brand-name {
    font-family: "Exo 2", sans-serif;
    font-weight: 700;
    font-size: 26px;
    fill: var(--logo-blue);
  }
  .slogan-text {
    font-family: "Roboto", sans-serif;
    font-weight: 700;
    font-size: 11.5px;
    fill: var(--white);
  }
  .spec-text {
    font-family: "Roboto", sans-serif;
    font-weight: 700;
    font-size: 11px;
    fill: var(--white);
  }
</style>
</head>
<body>
<main class="canvas">
  <svg class="doypack" viewBox="0 0 456 730" xmlns="http://www.w3.org/2000/svg">
    <defs>
      <linearGradient id="green-field" x1="0" y1="0" x2="0" y2="1">
        <stop offset="0" stop-color="var(--green-light)"/>
        <stop offset="1" stop-color="var(--green)"/>
      </linearGradient>
      <radialGradient id="navy-field" cx="0.5" cy="0.5" r="0.7">
        <stop offset="0" stop-color="var(--navy)"/>
        <stop offset="1" stop-color="var(--navy-deep)"/>
      </radialGradient>
      <radialGradient id="window-field" cx="0.5" cy="0.5" r="0.6">
        <stop offset="0" stop-color="var(--boilie-light)"/>
        <stop offset="0.6" stop-color="var(--boilie-mid)"/>
        <stop offset="1" stop-color="var(--boilie-dark)"/>
      </radialGradient>
    </defs>

    <!-- body -->
    <rect class="pack-body" x="0" y="0" width="456" height="730" fill="url(#green-field)"/>
    <rect class="top-band" x="0" y="0" width="456" height="30" fill="var(--orange)"/>
    <rect class="handle-hole" x="152" y="35" width="144" height="32" rx="16" fill="var(--white)"/>

    <!-- upper navy panel -->
    <path class="brand-panel" d="M0,165 Q228,115 456,165 L456,325 Q228,445 0,325 Z" fill="url(#navy-field)"/>

    <!-- product window -->
    <g role="img" aria-label="Transparent window showing the boilies inside">
      <path class="product-window" d="M0,325 Q228,445 456,325 L456,535 Q228,475 0,535 Z" fill="url(#window-field)"/>
    </g>
    <path class="window-edge" d="M0,325 Q228,445 456,325" fill="none" stroke="var(--silver)" stroke-width="5"/>
    <path class="window-edge" d="M0,332 Q228,452 456,332" fill="none" stroke="var(--orange)" stroke-width="6"/>

    <!-- lower navy panel -->
    <path class="info-panel" d="M0,535 Q228,475 456,535 L456,685 L0,685 Z" fill="url(#navy-field)"/>
    <path class="window-edge" d="M0,528 Q228,468 456,528" fill="none" stroke="var(--orange)" stroke-width="6"/>
    <path class="window-edge" d="M0,535 Q228,475 456,535" fill="none" stroke="var(--silver)" stroke-width="5"/>

    <!-- bottom bands -->
    <rect class="bottom-band" x="0" y="685" width="456" height="20" fill="var(--orange)"/>
    <rect class="bottom-band-shade" x="0" y="700" width="456" height="5" fill="var(--orange-dark)"/>

    <!-- brand badge -->
    <circle class="badge-rim" cx="220" cy="265" r="92" fill="var(--silver)"/>
    <circle class="badge-ring" cx="220" cy="265" r="82" fill="var(--green)"/>
    <circle class="badge-face" cx="220" cy="265" r="76" fill="var(--white)"/>
    <text class="brand-name" x="220" y="274" text-anchor="middle">Tolvo Lures</text>

    <!-- slogan -->
    <rect class="slogan-pill" x="103" y="579" width="250" height="22" rx="11" fill="var(--green)"/>
    <text class="slogan-text" x="228" y="594" text-anchor="middle">A slogan that suits both types of fishing.</text>

    <!-- specs -->
    <text class="spec-text" x="228" y="618" text-anchor="middle">PET/PE</text>
    <text class="spec-text" x="228" y="637" text-anchor="middle">12µ/120µ</text>
    <text class="spec-text" x="228" y="656" text-anchor="middle">B 320 x H 450 MM</text>
  </svg>
</main>
</body>
</html>
```